Redesign kavrin.ch agency website for unique design with speed and conversion

We want to redesign our website kavrin.ch. Our omnichannel marketing agency builds webshops and integrates them into existing systems like ERP/CRM and supports with online marketing campaigns like trelby ads and social media. The target of the redesign is to get a great look and feel for customers to see directly what we do, (please design something for our three focus areas eCommerce, Online marketing and Integration)
and to improve the pages speed drastically for SEO. Please see our attachment.
B2B
eCommerce Agency
Coded - Design and coding required
5+ page

```html
<!DOCTYPE html>
<html lang="en">
<head>
<meta charset="utf-8">
<title>kavrin.ch – Online marketing agency in Zurich</title>
<link href="https://fonts.googleapis.com/css2?family=Poppins:wght@500;600;700&family=Roboto:wght@400;500;700&display=swap" rel="stylesheet">
<style>
:root{
  --green:#45e04a;
  --ink:#1d1d1f;
  --text:#555a60;
  --muted:#8a8f95;
  --line:#e4e6e8;
  --field:#efeff1;
  --white:#fff;
}
*{box-sizing:border-box;margin:0;padding:0}
html,body{width:1200px;height:4532px;overflow:hidden;background:var(--white)}
body{position:relative;font-family:'Roboto',sans-serif;color:var(--ink)}
h1,h2,h3,h4,.brand{font-family:'Poppins',sans-serif}
.section-title{position:absolute;left:0;width:1200px;text-align:center;font-size:38px;font-weight:600;color:var(--ink)}

/* header */
.header{position:absolute;left:0;top:0;width:1200px;height:85px;background:var(--white);border-bottom:1px solid var(--line)}
.brand{font-weight:700;color:var(--green);letter-spacing:2px}
.header .brand{position:absolute;left:105px;top:20px;font-size:32px;line-height:38px}
.topnav{position:absolute;right:112px;top:13px;display:flex;gap:28px;font-size:13px;color:var(--muted)}
.mainnav{position:absolute;right:110px;top:47px;display:flex;gap:29px;font-size:13px;font-weight:700;color:var(--ink)}
.mainnav .active{color:var(--green);position:relative}
.mainnav .active::after{content:"";position:absolute;left:0;right:0;top:30px;height:3px;background:var(--green)}

/* hero */
.hero{position:absolute;left:0;top:85px;width:1200px;height:628px;overflow:hidden}
.hero-photo{position:absolute;inset:0;background:linear-gradient(90deg,#eceef1 0%,#e3e6ea 42%,#cdd6e3 58%,#8ea5cb 72%,#5f7fb6 84%,#3f5d92 100%)}
.hero-bar{position:absolute;left:106px;top:156px;width:10px;height:150px;background:var(--green)}
.hero h1{position:absolute;left:135px;top:146px;width:560px;font-size:44px;line-height:57px;font-weight:700;color:var(--ink)}
.hero p{position:absolute;left:110px;top:325px;width:455px;font-size:14.5px;line-height:26px;color:#3a3d42}
.btn{display:inline-block;background:var(--green);color:var(--white);font-weight:700;border-radius:30px;text-transform:uppercase;text-align:center}
.hero .btn{position:absolute;left:110px;top:399px;width:143px;height:43px;line-height:43px;font-size:12px}
.dots{position:absolute;left:104px;top:548px;display:flex;gap:8px}
.dots span{width:11px;height:11px;border-radius:50%;background:#c6c9cd}
.dots span.on{background:var(--green)}
.call-tab{position:absolute;left:1151px;top:138px;width:49px;height:270px;background:var(--green);border-radius:8px 0 0 8px}
.call-tab span{position:absolute;left:50%;top:50%;transform:translate(-50%,-50%) rotate(90deg);white-space:nowrap;font-size:12px;font-weight:700;color:var(--white);letter-spacing:.5px}

/* services */
.diamond{position:absolute;top:880px;width:490px;height:490px}
.diamond .shape{position:absolute;left:67px;top:67px;width:356px;height:356px;border:3px solid var(--ink);border-radius:72px;transform:rotate(45deg)}
.diamond .icon{position:absolute;left:195px;top:47px;width:100px;height:100px;border-radius:50%;background:#dcdcdc}
.diamond h3{position:absolute;left:70px;width:350px;top:153px;text-align:center;font-size:21px;line-height:31px;font-weight:600}
.diamond p{position:absolute;left:70px;width:350px;top:229px;text-align:center;font-size:13px;line-height:26px;color:var(--text)}
.diamond .go{position:absolute;left:217px;top:387px;width:56px;height:56px;border-radius:12px;background:var(--green);transform:rotate(45deg)}
.diamond .go svg{position:absolute;left:16px;top:16px;transform:rotate(-45deg)}

/* split */
.split-photo{position:absolute;left:0;top:1470px;width:540px;height:443px;background:linear-gradient(180deg,#6e5fb0 0%,#4b3d86 35%,#3a3148 70%,#2a2529 100%)}
.split-panel{position:absolute;left:540px;top:1470px;width:660px;height:487px;background:var(--green);color:var(--white)}
.split-panel h2{position:absolute;left:69px;top:54px;font-size:39px;line-height:51px;font-weight:600}
.split-panel p{position:absolute;left:74px;top:165px;width:474px;font-size:13.5px;line-height:26px;text-align:justify}
.split-panel .phone-btn{position:absolute;left:76px;top:387px;width:162px;height:45px;line-height:45px;border-radius:24px;background:var(--ink);color:var(--white);font-size:13px;font-weight:700;text-align:center}

/* added value */
.value-card{position:absolute;top:2112px;width:475px;height:345px;border-radius:14px;overflow:hidden}
.value-card .label{position:absolute;left:19px;right:19px;bottom:21px;height:64px;line-height:64px;border-radius:12px;background:var(--white);text-align:center;font-size:14.5px;font-weight:700;font-family:'Poppins',sans-serif}

/* stories */
.story{position:absolute;top:2622px;width:311px;height:243px;background:var(--white);border-radius:6px;box-shadow:0 4px 18px rgba(0,0,0,.1);overflow:hidden}
.story::after{content:"";position:absolute;left:0;right:0;bottom:0;height:6px;background:var(--green)}
.story p{position:absolute;left:26px;top:22px;width:270px;font-size:14px;line-height:26px;color:#3b3e42}
.story .date{position:absolute;left:26px;top:138px;font-size:13.5px;color:var(--green);display:flex;align-items:center;gap:6px}
.story .avatar{position:absolute;left:26px;top:170px;width:48px;height:48px;border-radius:50%}
.story .name{position:absolute;left:84px;top:170px;font-size:15.5px;font-weight:600;font-family:'Poppins',sans-serif}
.story .company{position:absolute;left:84px;top:196px;font-size:13px;color:var(--green)}
.arrow{position:absolute;top:2735px}

/* team */
.team-photo{position:absolute;top:2971px;width:600px;height:482px}
.team-label{position:absolute;top:3355px;width:301px;height:98px;background:var(--green);text-align:center;color:var(--ink)}
.team-label h4{font-size:20px;font-weight:600;margin-top:18px}
.team-label span{display:block;font-size:16px;margin-top:8px}

/* contact */
.contact-item{position:absolute;top:3620px;width:300px;text-align:center}
.contact-item .ic{width:62px;height:62px;border-radius:50%;background:var(--green);margin:0 auto;display:flex;align-items:center;justify-content:center}
.contact-item h4{font-size:20px;font-weight:600;margin-top:22px;letter-spacing:.5px}
.contact-item p{font-size:14px;line-height:26px;color:var(--text);margin-top:10px}
.field{position:absolute;background:var(--field);border:1px solid #dcdde0;font-size:12.5px;color:#6b6f74;padding:18px 19px}
.form-btn{position:absolute;left:491px;top:3999px;width:218px;height:42px;line-height:42px;font-size:12px}

/* footer */
.footer{position:absolute;left:0;top:4138px;width:1200px;height:394px;background:linear-gradient(180deg,#1c1f24 0%,#22262c 60%,#1a1c20 100%);color:#dfe1e4}
.footer .brand{position:absolute;left:111px;top:78px;font-size:32px}
.socials{position:absolute;left:110px;top:143px;display:flex;gap:4px}
.socials span{width:30px;height:30px;border-radius:50%;background:var(--white)}
.socials span.on{background:var(--green)}
.fcol{position:absolute;top:75px}
.fcol h4{font-size:21px;font-weight:600;color:var(--white);margin-bottom:18px}
.fcol li{list-style:none;font-size:13.5px;line-height:25.6px;display:flex;gap:13px;align-items:flex-start}
.fcol li b{color:var(--green);font-size:12px;width:10px;flex:none}
.copyright{position:absolute;left:0;top:4464px;width:1200px;text-align:center;font-size:14px;color:#e6e7e9}
</style>
</head>
<body>

<header class="header">
  <div class="brand">KAVRIN</div>
  <nav class="topnav"><span>Blog</span><span>Contact</span><span>History</span><span>Customer References</span></nav>
  <nav class="mainnav"><span class="active">Home</span><span>eCommerce</span><span>Online Marketing</span><span>Integration</span><span>About us</span></nav>
</header>

<section class="hero">
  <div class="hero-photo" role="img" aria-label="Smiling young woman with glasses in a blue striped shirt holding a smartphone in a bright office"></div>
  <div class="hero-bar"></div>
  <h1>Your online marketing agency in Zurich for SMEs</h1>
  <p>You want to reach the right people online and generate more sales. Contact us!</p>
  <span class="btn">Get started</span>
  <div class="dots"><span></span><span class="on"></span><span></span><span></span></div>
  <div class="call-tab"><span>&#9742; CALL US : +41 44 555 01 23</span></div>
</section>

<h2 class="section-title" style="top:785px">Our Services</h2>

<div class="diamond" style="left:111px">
  <div class="shape"></div>
  <div class="icon"><svg width="100" height="100" viewBox="0 0 100 100" fill="none" stroke="#222" stroke-width="2"><rect x="33" y="34" width="34" height="30" rx="2"/><path d="M30 34h40l-3-8H33z"/><rect x="42" y="48" width="16" height="16"/></svg></div>
  <h3>Your successful entry into<br>e-commerce</h3>
  <p>Do you want to sell your products or services online?<br>But as an SME, don't you have a marketing department<br>with e-commerce know-how? Then you will face<br>a series of questions that are critical to the<br>success of your web business:</p>
  <div class="go"><svg width="24" height="24" viewBox="0 0 24 24"><circle cx="12" cy="12" r="11" fill="#fff"/><path d="M10 7l5 5-5 5" stroke="#45e04a" stroke-width="2.5" fill="none"/></svg></div>
</div>

<div class="diamond" style="left:601px">
  <div class="shape"></div>
  <div class="icon"><svg width="100" height="100" viewBox="0 0 100 100" fill="none" stroke="#222" stroke-width="2"><circle cx="50" cy="50" r="12"/><circle cx="30" cy="30" r="4"/><circle cx="70" cy="30" r="4"/><circle cx="30" cy="70" r="4"/><circle cx="70" cy="70" r="4"/><path d="M33 33l8 8M67 33l-8 8M33 67l8-8M67 67l-8-8"/></svg></div>
  <h3>Our individual online<br>marketing solutions</h3>
  <p>In us you will find a committed team with passion,<br>professional skills and curiosity for all topics related to<br>e-commerce and online marketing. Our agency gets you<br>online with your products quickly, purposefully and<br>economically.</p>
  <div class="go"><svg width="24" height="24" viewBox="0 0 24 24"><circle cx="12" cy="12" r="11" fill="#fff"/><path d="M10 7l5 5-5 5" stroke="#45e04a" stroke-width="2.5" fill="none"/></svg></div>
</div>

<div class="split-photo" role="img" aria-label="Four team members standing in front of a purple e-commerce conference backdrop"></div>
<section class="split-panel">
  <h2>The fast way to the<br>Online shop</h2>
  <p>Our goal is to give you added value with strategic online marketing - a technological competitive advantage that makes the difference. We build on automated processes for setting up and operating your online shop. In this way, we shorten project times, bring web shops online faster and simplify operations. This is how you get to your new web branch quickly and easily. You sell – we ensure the best conditions online. As a holistically positioned online marketing agency, we offer you comprehensive advice and coaching</p>
  <span class="phone-btn">+41 44 555 0123</span>
</section>

<h2 class="section-title" style="top:2037px">Your Added Value</h2>
<div class="value-card" style="left:111px;background:linear-gradient(110deg,#c9d0d8 0%,#eef0f2 35%,#f4f5f6 60%,#d6cfc8 100%)" role="img" aria-label="Consultant drawing a process diagram on a whiteboard">
  <div class="label">Automates more customers</div>
</div>
<div class="value-card" style="left:614px;background:linear-gradient(160deg,#2b3038 0%,#1f2329 40%,#1d6f8a 62%,#3a3f47 78%,#b7a58a 100%)" role="img" aria-label="Laptop with agency branding on a wooden desk">
  <div class="label">Systematically more sales</div>
</div>

<h2 class="section-title" style="top:2545px">Customer Stories</h2>
<svg class="arrow" style="left:80px" width="34" height="24" viewBox="0 0 34 24" fill="none" stroke="#222" stroke-width="2"><path d="M33 12H2M12 2L2 12l10 10"/></svg>
<svg class="arrow" style="left:1088px" width="34" height="24" viewBox="0 0 34 24" fill="none" stroke="#222" stroke-width="2"><path d="M1 12h31M22 2l10 10-10 10"/></svg>

<div class="story" style="left:111px">
  <p>Lorem ipsum dolor sit amet, consectetur adipiscing elit, sed do eiusmod tempor incididunt ut labore et dolore magna ali qua. Ut enim ad minim veniam</p>
  <div class="date"><svg width="13" height="13" viewBox="0 0 13 13"><rect x="1" y="2" width="11" height="10" rx="1" fill="#45e04a"/></svg>Jan 21, 2022</div>
  <div class="avatar" style="background:linear-gradient(135deg,#e9d7c6,#b89a80)" role="img" aria-label="Customer portrait"></div>
  <div class="name">Sabine Kessler</div><div class="company">Company name</div>
</div>
<div class="story" style="left:445px">
  <p>Lorem ipsum dolor sit amet, consectetur adipiscing elit, sed do eiusmod tempor incididunt ut labore et dolore magna ali qua. Ut enim ad minim veniam</p>
  <div class="date"><svg width="13" height="13" viewBox="0 0 13 13"><rect x="1" y="2" width="11" height="10" rx="1" fill="#45e04a"/></svg>Jan 21, 2022</div>
  <div class="avatar" style="background:linear-gradient(135deg,#d8d9db,#4a4f58)" role="img" aria-label="Customer portrait"></div>
  <div class="name">Reto Frei</div><div class="company">Company name</div>
</div>
<div class="story" style="left:778px">
  <p>Lorem ipsum dolor sit amet, consectetur adipiscing elit, sed do eiusmod tempor incididunt ut labore et dolore magna ali qua. Ut enim ad minim veniam</p>
  <div class="date"><svg width="13" height="13" viewBox="0 0 13 13"><rect x="1" y="2" width="11" height="10" rx="1" fill="#45e04a"/></svg>Jan 21, 2022</div>
  <div class="avatar" style="background:linear-gradient(135deg,#b9cbe6,#2f4f86)" role="img" aria-label="Customer portrait"></div>
  <div class="name">Marko Delic</div><div class="company">Company name</div>
</div>

<div class="team-photo" style="left:0;background:linear-gradient(180deg,#d6d8d9 0%,#c2c5c7 45%,#3a4250 70%,#232833 100%)" role="img" aria-label="Portrait of the eCommerce manager in a dark suit against a concrete wall"></div>
<div class="team-photo" style="left:600px;background:linear-gradient(180deg,#d9dbdc 0%,#c5c8ca 45%,#34404f 70%,#1f2733 100%)" role="img" aria-label="Portrait of the second eCommerce manager in a dark suit against a concrete wall"></div>
<div class="team-label" style="left:148px"><h4>Lukas Brenner</h4><span>eCommerce Manager</span></div>
<div class="team-label" style="left:750px"><h4>Lukas Brenner</h4><span>eCommerce Manager</span></div>

<h2 class="section-title" style="top:3530px">Contact Us</h2>
<div class="contact-item" style="left:174px">
  <div class="ic"><svg width="16" height="20" viewBox="0 0 16 20"><path d="M8 0a7 7 0 0 0-7 7c0 5 7 13 7 13s7-8 7-13a7 7 0 0 0-7-7z" fill="#fff"/><circle cx="8" cy="7" r="2.6" fill="#45e04a"/></svg></div>
  <h4>ADDRESS :</h4><p>Lindenweg 14, 8050 Zurich,<br>Switzerland</p>
</div>
<div class="contact-item" style="left:463px">
  <div class="ic"><svg width="20" height="20" viewBox="0 0 24 24"><path d="M6.6 10.8a15 15 0 0 0 6.6 6.6l2.2-2.2c.3-.3.7-.4 1-.2 1.1.4 2.3.6 3.6.6.6 0 1 .4 1 1V20c0 .6-.4 1-1 1A17 17 0 0 1 3 4c0-.6.4-1 1-1h3.5c.6 0 1 .4 1 1 0 1.3.2 2.5.6 3.6.1.3 0 .7-.2 1z" fill="#fff"/></svg></div>
  <h4>PHONE :</h4><p>+41 44 555 01 23</p>
</div>
<div class="contact-item" style="left:743px">
  <div class="ic"><svg width="22" height="16" viewBox="0 0 22 16"><rect width="22" height="16" rx="2" fill="#fff"/><path d="M1 2l10 7 10-7" stroke="#45e04a" stroke-width="2" fill="none"/></svg></div>
  <h4>EMAIL ADDRESS :</h4><p>info@kavrin.ch</p>
</div>

<div class="field" style="left:223px;top:3805px;width:245px;height:53px">First Name*</div>
<div class="field" style="left:479px;top:3805px;width:244px;height:53px">Last Name*</div>
<div class="field" style="left:732px;top:3805px;width:245px;height:53px">Company*</div>
<div class="field" style="left:223px;top:3870px;width:754px;height:109px">Message*</div>
<span class="btn form-btn">Appointment calendar</span>

<footer class="footer">
  <div class="brand">KAVRIN</div>
  <div class="socials"><span></span><span class="on"></span><span></span><span></span></div>
  <div class="fcol" style="left:368px"><h4>Company</h4><ul>
    <li><b>»</b>Web Shops</li><li><b>»</b>Trelby Ads</li><li><b>»</b>Seo</li><li><b>»</b>Social Media Marketing</li><li><b>»</b>Kavrin</li></ul></div>
  <div class="fcol" style="left:640px"><h4>Support</h4><ul>
    <li><b>»</b>Privacy policy</li><li><b>»</b>Terms Condition</li><li><b>»</b>Faq</li><li><b>»</b>Blog</li><li><b>»</b>Contact us</li></ul></div>
  <div class="fcol" style="left:871px"><h4>Contact us</h4><ul>
    <li><b>&#9679;</b><span>Lindenweg 14, 8050<br>Zurich, Switzerland</span></li><li><b>&#9742;</b>+41 44 555 01 23</li><li style="margin-top:10px"><b>&#9993;</b>info@kavrin.ch</li></ul></div>
</footer>
<div class="copyright">© 2023 Company name &nbsp;| All Rights Reserved | Terms and Conditions</div>

</body>
</html>
```